Hollow Thicket, a 3d voxel survival video game needs a card for gaming conventions

I am the lead developer for Hollow Thicket http://www.HollowThicket.example and need a business card to hand out at an indie gaming convention
The card would need to include the game name, website url, my name, position (Lead Developer), e-mail and phone number
The game is a 3d, voxel (with smooth terrain) based survival game with guns and wildlife. The main icon of the game would likely be a grizzly bear but I am willing to accept other designs too.
Attached is a media kit for the game with some images you can use but don't have to its just what little art I can provide. Anything on the website or from the video game can also be used. unrelated art can also be used.
Target Market(s)
Indie Developers/publishers at conferences
Industry/Entity Type
Games
Contact Information for Business Card
Name: Corin Waldrick
Position: Lead Developer
E-mail: Pale_Kettle@mailbox.example
Phone number: 555-372-1186

```html
<!DOCTYPE html>
<html lang="en">
<head>
<meta charset="utf-8">
<title>Hollow Thicket — Business Card</title>
<link rel="stylesheet" href="https://fonts.googleapis.com/css2?family=Source+Sans+3:wght@400;600;800&display=swap">
<style>
  :root {
    --stage-top: #a9a9a9;
    --stage-bottom: #939393;
    --front-top: #a5180b;
    --front-mid: #a9573a;
    --front-bottom: #b39558;
    --ink-light: #ffffff;
    --logo-cream: #e9d8a2;
    --bear-dark: #3b2a1c;
    --bear-mid: #6e4e33;
    --scene-sky: #2d3f66;
    --scene-mount: #3a3a3e;
    --scene-grass: #3f5a2a;
    --scene-water: #2f3f55;
    --scene-shore: #3a3a3c;
  }
  * { box-sizing: border-box; margin: 0; padding: 0; }
  html, body { width: 1200px; height: 900px; overflow: hidden; }
  body {
    background: linear-gradient(180deg, var(--stage-top), var(--stage-bottom));
    font-family: "Source Sans 3", "Myriad Pro", sans-serif;
    position: relative;
  }
  .card {
    position: absolute;
    top: 306px;
    width: 440px;
    height: 271px;
    border-radius: 10px;
    overflow: hidden;
  }
  .card--front {
    left: 149px;
    background: linear-gradient(180deg, var(--front-top) 0%, var(--front-mid) 50%, var(--front-bottom) 100%);
  }
  .card--back { left: 608px; }

  .wordmark {
    position: absolute;
    color: var(--logo-cream);
    font-weight: 800;
    text-transform: uppercase;
    letter-spacing: 4px;
    line-height: 0.95;
  }
  .card--front .wordmark {
    left: 26px;
    top: 36px;
    font-size: 48px;
  }
  .card--back .wordmark {
    left: 0; right: 0;
    top: 62px;
    text-align: center;
    font-size: 60px;
  }

  .bear-photo {
    position: absolute;
    left: 296px;
    top: 46px;
    width: 144px;
    height: 225px;
    background: radial-gradient(ellipse at 45% 30%, var(--bear-mid), var(--bear-dark) 75%);
    border-radius: 60px 30px 0 0;
  }

  .holder {
    position: absolute;
    left: 33px;
    top: 171px;
    color: var(--ink-light);
  }
  .holder__name { font-size: 15.5px; font-weight: 600; line-height: 1.1; }
  .holder__role { font-size: 12.5px; font-weight: 400; line-height: 1.2; }

  .contact {
    position: absolute;
    left: 33px;
    top: 221px;
    list-style: none;
    color: var(--ink-light);
    font-size: 12.5px;
    line-height: 16px;
  }
  .contact__item { display: flex; align-items: center; gap: 6px; }
  .contact__icon { width: 9px; height: 9px; fill: var(--ink-light); flex: none; }

  .game-scene {
    position: absolute;
    inset: 0;
    background:
      radial-gradient(ellipse at 30% 25%, var(--scene-mount) 0%, transparent 35%),
      linear-gradient(180deg, var(--scene-sky) 0%, var(--scene-sky) 25%, var(--scene-grass) 40%, var(--scene-water) 55%, var(--scene-shore) 100%);
  }
  .site-url {
    position: absolute;
    left: 0; right: 0;
    bottom: 16px;
    text-align: center;
    color: var(--logo-cream);
    font-size: 13px;
    font-weight: 600;
    letter-spacing: 0.5px;
  }
</style>
</head>
<body>
  <section class="card card--front">
    <div class="wordmark">Hollow<br>Thicket</div>
    <div class="bear-photo" role="img" aria-label="Photograph of a roaring grizzly bear"></div>
    <div class="holder">
      <p class="holder__name">Corin Waldrick</p>
      <p class="holder__role">Lead Developer</p>
    </div>
    <ul class="contact">
      <li class="contact__item">
        <svg class="contact__icon" viewBox="0 0 24 24" aria-hidden="true"><path d="M6.6 10.8a15.1 15.1 0 0 0 6.6 6.6l2.2-2.2a1 1 0 0 1 1-.25 11.4 11.4 0 0 0 3.6.57 1 1 0 0 1 1 1V20a1 1 0 0 1-1 1A17 17 0 0 1 3 4a1 1 0 0 1 1-1h3.5a1 1 0 0 1 1 1c0 1.25.2 2.45.57 3.57a1 1 0 0 1-.25 1z"/></svg>
        555-372-1186
      </li>
      <li class="contact__item">
        <svg class="contact__icon" viewBox="0 0 24 24" aria-hidden="true"><path d="M2 5h20v2l-10 7L2 7z"/><path d="M2 9l10 7 10-7v10H2z"/></svg>
        Pale_Kettle@mailbox.example
      </li>
    </ul>
  </section>

  <section class="card card--back">
    <div class="game-scene" role="img" aria-label="In-game landscape with mountains, pine trees and a river at dusk"></div>
    <div class="wordmark">Hollow<br>Thicket</div>
    <p class="site-url">www.HollowThicket.example</p>
  </section>
</body>
</html>
```